Velmora Consulting Business

** Please add the content information from my old business card
1. I would like to see a two sided business card with both options with the 1st Option--Tallow Spire-new WHITE BACKGROUND LOGO
2 nd Option-Tallow Spire - new BLACK- Background Logo
3rd -Option a business card with my Photo on the card
Please add the new word to the card information:
EXECUTION
AS THE OWNER'S REP
WE AIM TO ACHIEVE YOUR
INFRASTRUCTURE VISION with
OUR SPECIALIZATION & EXECUTION in:

FUNDING Planning
BUSINESS Planning
INFRASTRUCTURE Planning
PROJECT Management
Since 2012
_____________________________________________________________________
I want to get spot uv raised printing. I was liking a a nice rich white linen paper stock with black writing & NOT A COLORED CARD other than a variety of white or black cards concept

```html
<!DOCTYPE html>
<html lang="en">
<head>
<meta charset="utf-8">
<title>Velmora Consulting – Business Card</title>
<link rel="stylesheet" href="https://fonts.googleapis.com/css2?family=Montserrat:wght@400;500;700;800&display=swap">
<style>
  :root {
    --stage: #262626;
    --paper: #ffffff;
    --ink: #1d1d1d;
    --red: #e3202f;
    --photo-hair: #c4834f;
    --photo-skin: #e6bfa3;
    --photo-top: #151515;
  }
  * { box-sizing: border-box; margin: 0; padding: 0; }
  html, body { width: 1200px; height: 900px; overflow: hidden; }
  body {
    background: var(--stage);
    font-family: "Montserrat", sans-serif;
    color: var(--ink);
    position: relative;
  }
  .card {
    position: absolute;
    left: 280px;
    width: 640px;
    height: 366px;
    background: var(--paper);
    border-radius: 24px;
    overflow: hidden;
  }
  .card--back { top: 64px; }
  .card--front { top: 470px; }

  /* wordmark */
  .wordmark { position: absolute; }
  .wordmark__name {
    display: flex;
    align-items: center;
    gap: 8px;
    font-weight: 700;
    line-height: 1;
    color: var(--ink);
  }
  .wordmark__dot {
    display: inline-block;
    background: var(--red);
    border-radius: 50%;
  }
  .wordmark__tag {
    font-weight: 500;
    letter-spacing: 0.62em;
    margin-top: 8px;
    color: var(--ink);
  }

  .card--back .wordmark { left: 42px; top: 142px; }
  .card--back .wordmark__name { font-size: 56px; }
  .card--back .wordmark__dot { width: 14px; height: 14px; }
  .card--back .wordmark__tag { font-size: 14px; }

  .divider {
    position: absolute;
    left: 318px;
    top: 80px;
    width: 1.5px;
    height: 206px;
    background: var(--red);
  }
  .mission {
    position: absolute;
    left: 342px;
    top: 82px;
    width: 280px;
  }
  .mission__lead {
    color: var(--red);
    font-weight: 800;
    font-size: 12.5px;
    line-height: 1.35;
    text-transform: uppercase;
  }
  .mission__lead span { text-transform: none; }
  .services {
    list-style: none;
    margin-top: 18px;
    font-size: 14px;
    line-height: 1.65;
    font-weight: 500;
  }

  /* front */
  .card--front .wordmark { left: 40px; top: 46px; }
  .card--front .wordmark__name { font-size: 46px; }
  .card--front .wordmark__dot { width: 12px; height: 12px; }
  .card--front .wordmark__tag { font-size: 12px; }

  .person { position: absolute; left: 40px; top: 150px; }
  .person__name {
    color: var(--red);
    font-weight: 700;
    font-size: 27px;
    line-height: 1.1;
  }
  .person__title {
    font-size: 13px;
    font-weight: 500;
    text-transform: uppercase;
    margin-top: 4px;
  }
  .person__places { font-size: 15px; font-weight: 500; margin-top: 28px; }
  .contact { list-style: none; margin-top: 10px; }
  .contact li {
    display: flex;
    align-items: center;
    gap: 12px;
    font-size: 15px;
    font-weight: 500;
    line-height: 1.7;
  }
  .contact svg { width: 15px; height: 15px; fill: var(--red); flex: none; }

  .portrait {
    position: absolute;
    right: 0;
    top: 0;
    width: 250px;
    height: 100%;
    background: linear-gradient(180deg, var(--paper) 0%, var(--photo-hair) 12%, var(--photo-skin) 34%, var(--photo-top) 52%, var(--photo-top) 100%);
  }
</style>
</head>
<body>

<section class="card card--back">
  <div class="wordmark">
    <div class="wordmark__name">Velmora<span class="wordmark__dot"></span></div>
    <div class="wordmark__tag">CONSULTING</div>
  </div>
  <div class="divider"></div>
  <div class="mission">
    <p class="mission__lead">As the owner's rep<br>we aim to achieve your<br>infrastructure vision <span>with</span><br>our specialization <span>in:</span></p>
    <ul class="services">
      <li>FUNDING Planning</li>
      <li>BUSINESS Planning</li>
      <li>INFRASTRUCTURE Planning</li>
      <li>PROJECT Management</li>
      <li>Since 2012</li>
    </ul>
  </div>
</section>

<section class="card card--front">
  <div class="wordmark">
    <div class="wordmark__name">Velmora<span class="wordmark__dot"></span></div>
    <div class="wordmark__tag">CONSULTING</div>
  </div>
  <div class="person">
    <h1 class="person__name">Marisol Danvers-Okoye</h1>
    <p class="person__title">CEO / Lead Project Manager</p>
    <p class="person__places">Northhaven NT · Elmbrook NB</p>
    <ul class="contact">
      <li>
        <svg viewBox="0 0 24 24" aria-hidden="true"><path d="M6.6 10.8a15.1 15.1 0 0 0 6.6 6.6l2.2-2.2c.3-.3.7-.4 1-.2 1.1.4 2.3.6 3.6.6.6 0 1 .4 1 1V20c0 .6-.4 1-1 1A17 17 0 0 1 3 4c0-.6.4-1 1-1h3.5c.6 0 1 .4 1 1 0 1.3.2 2.5.6 3.6.1.3 0 .7-.2 1z"/></svg>
        867.555.0192
      </li>
      <li>
        <svg viewBox="0 0 24 24" aria-hidden="true"><path d="M2 5h20v14H2z M2 5l10 7 10-7" stroke="#fff" stroke-width="1.5"/></svg>
        marisol@velmora.ca
      </li>
      <li>
        <svg viewBox="0 0 24 24" aria-hidden="true"><circle cx="12" cy="12" r="10"/><path d="M2 12h20M12 2c3 3 3 17 0 20M12 2c-3 3-3 17 0 20" stroke="#fff" stroke-width="1.3" fill="none"/></svg>
        www.velmora.ca
      </li>
    </ul>
  </div>
  <div class="portrait" role="img" aria-label="Portrait photo of the CEO in a black top with arms crossed, on a white backdrop"></div>
</section>

</body>
</html>
```